Web Site Design for a Finance (lending) Company

We are opening a new subsidiary that focuses on lending money in the real estate industry. We need a web site designed to represent the business.

The business is lending money to real estate investors. A typical client/borrower will be looking to borrow money to buy a house, renovate it and then sell it at a profit, all within 12 months or less.

Company name is RTV Finance. Our logo is attached.

Attached is a general outline for the web site. We're working on writing more text for each page but this should give you enough to get started with some ideas.

Competitor web site that I like a lot (as an example): https://dorvaleqcapital.example/. Many of the general items on this site match what we will need (description of loan programs, FAQ)

Target Market(s)

Real estate investors (generally individuals or small companies with just a few people) who are buying homes, renovating them and then selling them at a profit.

Industry/Entity Type

Finance

Coding

Coded - Design and coding required

Number of Pages Required

5+ page

Colors

Designer to choose colors to be used in the design.

Requirements
Must have
• Minimalist design. Clean lines without too much clutter. Some stock photography is ok but the photos should not be distracting. They should almost fade in to the background so that user can focus on the key information about what our company does instead. We are a finance company, not a design company, so the information about our products will be more interesting to site visitors than the art.
• Some minimalist examples from Snapboard:
• https://www.snapboardia.example/explore/minimalist-web-design/
Nice to have
• If you search in zoovle for "hard money lenders" you will find many examples of web sites from our competition. I have provided a link above to competitor web site that I like a lot.
• I have attached our logo in EPS format. Logo is green. Web site doesn't have to be green but it should be of a color that will work well with the logo.

```html
<!DOCTYPE html>
<html lang="en">
<head>
<meta charset="utf-8">
<title>RTV Finance – About Us</title>
<link href="https://fonts.googleapis.com/css2?family=Lato:wght@400;700&family=Open+Sans:wght@300;400&family=Roboto:wght@500&display=swap" rel="stylesheet">
<style>
:root{
  --green:#014d2f;
  --green-dark:#013a23;
  --page-bg:#f4f4f4;
  --white:#ffffff;
  --heading:#333333;
  --body-text:#6b6b6b;
  --black:#151515;
  --rule:#2c6a4f;
}
*{margin:0;padding:0;box-sizing:border-box}
html,body{width:1009px;height:1200px;overflow:hidden}
body{background:var(--page-bg);font-family:'Open Sans',sans-serif;position:relative}
a{color:inherit;text-decoration:none}

.site-header{height:68px;background:var(--white);position:relative}
.brand{position:absolute;left:134px;top:20px;display:flex;align-items:center;gap:8px;
  font-family:'Lato',sans-serif;font-weight:700;font-size:20px;color:var(--green)}
.brand-mark{width:22px;height:22px;background:var(--green)}
.call{position:absolute;left:671px;top:15px;display:flex;align-items:center;gap:6px;color:var(--green)}
.call-icon{width:35px;height:35px;background:var(--green);border-radius:6px;display:flex;align-items:center;justify-content:center}
.call-text{font-family:'Lato',sans-serif;font-weight:700;line-height:1}
.call-label{font-size:22px;letter-spacing:.3px}
.call-number{font-size:15px;color:#1c3b2c;margin-top:1px}

.main-nav{height:36px;background:var(--green);position:relative}
.nav-links{position:absolute;left:134px;top:0;height:36px;display:flex;align-items:center;list-style:none;
  font-family:'Roboto',sans-serif;font-weight:500;font-size:12px;color:var(--white)}
.nav-links li{margin-right:27px}
.nav-links li:nth-child(4){margin-right:19px}
.nav-social{position:absolute;left:801px;top:8px;display:flex;gap:7px}
.nav-social span{width:20px;height:20px;background:var(--white);border-radius:3px}

.content{padding:0 134px}
.section-title{font-family:'Lato',sans-serif;font-weight:400;font-size:27px;color:var(--heading)}
.company{padding-top:34px}
.company p{font-weight:300;font-size:12.2px;line-height:20px;color:var(--body-text);margin-top:20px;width:735px}
.company .section-title+p{margin-top:10px}
.team{margin-top:38px}
.member{display:flex;margin-top:14px}
.member+.member{margin-top:29px}
.photo-frame{width:230px;height:215px;background:var(--white);padding:6px;box-shadow:0 0 3px rgba(0,0,0,.12);flex-shrink:0}
.photo{width:218px;height:203px}
.photo-evan{background:linear-gradient(135deg,#9aa39a 0%,#d7b49a 45%,#e7e2ea 100%)}
.photo-noah{background:linear-gradient(160deg,#5d5f66 0%,#6b5a55 50%,#2a2a2e 100%)}
.bio{margin-left:22px;width:480px}
.bio-name{font-family:'Lato',sans-serif;font-weight:400;font-size:27px;color:var(--green);margin-top:4px;margin-left:-2px}
.bio p{font-weight:300;font-size:12.2px;line-height:20px;color:var(--body-text);margin-top:20px}
.bio .bio-name+p{margin-top:4px}

.site-footer{position:absolute;left:0;top:942px;width:1009px;height:258px;background:var(--green);color:var(--white);font-family:'Lato',sans-serif}
.footer-col{position:absolute;top:45px}
.footer-col h3{font-weight:400;font-size:24px;letter-spacing:.3px;text-transform:uppercase}
.footer-col ul{list-style:none;margin-top:18px;margin-left:2px}
.footer-col li{font-size:14.5px;line-height:28px;text-transform:uppercase}
.col-info{left:105px}.col-booking{left:255px}.col-links{left:401px}.col-connect{left:642px}
.signup{display:flex;margin-top:20px;margin-left:1px}
.signup-email{width:164px;height:35px;background:var(--white);color:#444;font-size:12px;padding:11px 10px;font-family:'Open Sans',sans-serif}
.signup-button{width:93px;height:35px;background:var(--black);font-weight:700;font-size:16px;display:flex;align-items:center;justify-content:center}
.footer-social{display:flex;gap:6px;margin-top:18px;margin-left:1px}
.footer-social span{width:28px;height:28px;border:1.5px solid var(--white);border-radius:50%}
.footer-rule{position:absolute;left:0;top:206px;width:1009px;height:1px;background:var(--rule)}
.copyright{position:absolute;left:106px;top:228px;font-size:12px;font-weight:700}
.live-chat{position:absolute;left:630px;top:224px;width:269px;height:34px;background:var(--green-dark);display:flex;align-items:center;padding:0 10px;font-size:12px;font-weight:700}
.chat-controls{margin-left:auto;display:flex;gap:6px}
.chat-controls span{width:17px;height:15px;background:#0d6a40;border-radius:2px;display:flex;align-items:center;justify-content:center}
</style>
</head>
<body>
<header class="site-header">
  <a class="brand" href="#"><span class="brand-mark"></span>RTV Finance</a>
  <div class="call">
    <span class="call-icon">
      <svg width="22" height="22" viewBox="0 0 24 24"><path fill="#fff" d="M6.6 10.8a15.1 15.1 0 0 0 6.6 6.6l2.2-2.2a1 1 0 0 1 1-.25 11.4 11.4 0 0 0 3.6.57 1 1 0 0 1 1 1V20a1 1 0 0 1-1 1A17 17 0 0 1 3 4a1 1 0 0 1 1-1h3.5a1 1 0 0 1 1 1c0 1.25.2 2.45.57 3.57a1 1 0 0 1-.25 1z"/></svg>
    </span>
    <div class="call-text">
      <div class="call-label">CALL US</div>
      <div class="call-number">555-012-LOAN (5626)</div>
    </div>
  </div>
</header>

<nav class="main-nav">
  <ul class="nav-links">
    <li>HOME</li><li>ABOUT US</li><li>LOAN</li><li>RESOURCES</li><li>CONTACT US</li>
  </ul>
  <div class="nav-social"><span></span><span></span><span></span></div>
</nav>

<main class="content">
  <section class="company">
    <h1 class="section-title">The Company</h1>
    <p>Our team recognizes the social and economic impact that you have on communities as a borrower, and we’re proud to play a role in this process. We’re committed to serving you and exist to help you succeed with each investment property that you undertake.</p>
    <p>Excellence and integrity permeate every aspect of our business, giving us the ability to add value while mitigating risk, and we possess the moral courage to carry out those principles every day.</p>
    <p>Ultimately, our mission is to become America’s most respected lender for real estate investors. We strive towards this goal by delivering exceptional customer service and offering reasonable pricing through superior execution.</p>
  </section>

  <section class="team">
    <h2 class="section-title">The Team</h2>
    <article class="member">
      <div class="photo-frame"><div class="photo photo-evan" role="img" aria-label="Portrait photo of Evan, smiling in a light striped shirt by a window"></div></div>
      <div class="bio">
        <h3 class="bio-name">Evan Bio</h3>
        <p>Lorem ipsum dolor sit amet, consectetuer adipiscing elit, sed diam nonummy nibh euismod tincidunt ut laoreet dolore magna aliquam erat volutpat. Ut wisi enim ad minim veniam, quis nostrud exerci tation ullamcorper suscipit lobortis nisl ut aliquip ex ea commodo consequat.</p>
        <p>Duis autem vel eum iriure dolor in hendrerit in vulputate velit esse molestie consequat, vel illum dolore eu feugiat nulla facilisis at vero eros et accumsan et iusto odio dignissim qui blandit praesent luptatum zzril delenit augue duis dolore te feugait nulla facilisi.</p>
      </div>
    </article>
    <article class="member">
      <div class="photo-frame"><div class="photo photo-noah" role="img" aria-label="Portrait photo of Noah in a dark suit and red tie on a grey backdrop"></div></div>
      <div class="bio">
        <h3 class="bio-name">Noah Bio</h3>
        <p>Lorem ipsum dolor sit amet, consectetuer adipiscing elit, sed diam nonummy nibh euismod tincidunt ut laoreet dolore magna aliquam erat volutpat. Ut wisi enim ad minim veniam, quis nostrud exerci tation ullamcorper suscipit lobortis nisl ut aliquip ex ea commodo consequat.</p>
        <p>Duis autem vel eum iriure dolor in hendrerit in vulputate velit esse molestie consequat, vel illum dolore eu feugiat nulla facilisis at vero eros et accumsan et iusto odio dignissim qui blandit praesent luptatum zzril delenit augue duis dolore te feugait nulla facilisi.</p>
      </div>
    </article>
  </section>
</main>

<footer class="site-footer">
  <div class="footer-col col-info"><h3>Our Info</h3><ul><li>Homepage</li><li>About Us</li><li>Hiring</li></ul></div>
  <div class="footer-col col-booking"><h3>Booking</h3><ul><li>Booking Page</li><li>Blog</li></ul></div>
  <div class="footer-col col-links"><h3>Additional Links</h3><ul><li>Gift Card</li><li>Help</li><li>We’re Green</li></ul></div>
  <div class="footer-col col-connect">
    <h3>Stay Connected</h3>
    <div class="signup"><div class="signup-email">EMAIL</div><div class="signup-button">SIGN UP</div></div>
    <div class="footer-social"><span></span><span></span><span></span><span></span></div>
  </div>
  <div class="footer-rule"></div>
  <div class="copyright">Copyright RTV @2017</div>
  <div class="live-chat">Live Chat
    <div class="chat-controls">
      <span><svg width="9" height="9" viewBox="0 0 10 10"><circle cx="5" cy="5" r="5" fill="#fff"/><path d="M2.8 4l2.2 2.2L7.2 4" stroke="#0d6a40" stroke-width="1.4" fill="none"/></svg></span>
      <span><svg width="9" height="9" viewBox="0 0 10 10"><path d="M5 1v8M1 5h8" stroke="#fff" stroke-width="2"/></svg></span>
    </div>
  </div>
</footer>
</body>
</html>
```